Norvane Freight and Provision Service Brochure

Please see http://www.norvanefreight.example for who we are and what we do.
We would like to see a design that matches the industry we work in i.e. Oil and Gas. The design should communicate large, heavy field operations, supply of vast bulk fuel quantities to our US and Afghan Military customers, plus financial independence and the companies whatever it takes attitude operation in remote often hostile areas. Dark colors like on the website - contrasting our green logo. A strong focus on our past performance/past experience.

Target Market(s)

Military Customers, Partners, Subcontractors

Industry/Entity Type

Industry

Contact Information for Business Card

Display of Address, Phone, email etc. of our 4 offices

Font styles to use
Sans Serif

Requirements
Must have
• Glossy brochure, modern, cool design. Great display (map) of our offices in the Middle East, Europe and Central Asia. A focus on our past performance/past experience. Customer logos/references
Nice to have
• Prominent highlighted watermark logo
Should not have
• Standard A4/Letter brochure

```html
<!DOCTYPE html>
<html lang="en">
<head>
<meta charset="utf-8">
<title>Norvane Freight and Provision – Our Projects</title>
<link rel="stylesheet" href="https://fonts.googleapis.com/css2?family=Mulish:wght@400;600;700;800&display=swap">
<style>
  :root {
    --stage: #d9d6d1;
    --panel-grey: #5a6061;
    --panel-blue: #15466c;
    --heading-yellow: #f2e63a;
    --text-white: #ffffff;
    --sky-top: #2f78b8;
    --sky-mid: #8fb3cf;
    --dusk-orange: #f0a04a;
    --plant-dark: #1c2230;
    --water-gold: #b98a2a;
  }
  * { margin: 0; padding: 0; box-sizing: border-box; }
  html, body { width: 1200px; height: 579px; overflow: hidden; background: var(--stage); }
  body { font-family: "Mulish", Arial, sans-serif; color: var(--text-white); position: relative; }

  .spread { position: absolute; left: 32px; top: 50px; width: 1136px; height: 488px; display: flex; box-shadow: 0 2px 8px rgba(0,0,0,.25); }
  .panel { position: relative; height: 100%; }
  .panel--grey { width: 391px; background: var(--panel-grey); }
  .panel--photo { width: 363px; }
  .panel--blue { width: 382px; background: var(--panel-blue); }

  .panel-title { position: absolute; top: 26px; font-size: 22px; font-weight: 800; letter-spacing: .3px; }
  .project-heading { position: absolute; color: var(--heading-yellow); font-size: 13.5px; font-weight: 700; line-height: 17px; }
  .project-body { position: absolute; font-size: 6.5px; line-height: 8.1px; text-align: justify; font-weight: 600; }
  .project-photo { float: left; margin: 0 7px 2px 0; }

  .refinery-photo { width: 100%; height: 100%;
    background: linear-gradient(180deg, var(--sky-top) 0%, var(--sky-mid) 30%, var(--dusk-orange) 52%, var(--plant-dark) 62%, var(--plant-dark) 66%, var(--water-gold) 78%, var(--plant-dark) 100%); }
</style>
</head>
<body>
<main class="spread">

  <section class="panel panel--grey">
    <h2 class="panel-title" style="left:28px;">OUR PROJECTS</h2>

    <h3 class="project-heading" style="left:28px; top:72px; width:350px;">MoD - AAF Aviation Fuel Supply Contract - Contract Number W71QRX-14-D-0027</h3>
    <div class="project-body" style="left:28px; top:128px; width:340px;">
      <div class="project-photo" role="img" aria-label="Photo of a fuel nozzle being handled by a soldier" style="width:108px; height:76px; background:linear-gradient(135deg,#3b3f44,#7a6a5c 60%,#2a2c30);"></div>
      We are an incumbent contractor for this requirement of the Ministry of Defence of Afghanistan and we have performed our duties exceptionally well. This contract is the primary support mechanism for Afghan Air Force (AAF) requirements throughout Afghanistan and for all Direct-Into-Plane (Into-Aircraft) fuel requirements of the AAF. Norvane fulfils the Government requirements according to terms established in the basic contract and resulting delivery orders. We accomplish all required commodity sourcing and transportation services to delivery points specified in resulting requests for service on a on a free on board (F.O.B.) Destination basis.
    </div>

    <h3 class="project-heading" style="left:28px; top:248px; width:350px;">Bulk Diesel Supply to Kandahar Power Plants - Contract Number: W71QRX-15-C-0009</h3>
    <div class="project-body" style="left:28px; top:305px; width:340px;">
      <div class="project-photo" role="img" aria-label="Photo of a national flag held up against the sky" style="width:108px; height:77px; background:linear-gradient(160deg,#2c4a78,#1a2030 55%,#6b2020);"></div>
      The contract is a primary support mechanism for fuel requirements of the KGPA Kandahar Bridging Solution (KBS) power generation. It provides fuel for the operation of the two (2) diesel power plants built under the KBS program which are located at Shurandam Industrial Park (SIP) and Bagh-e-Pol (BEP). The fuel will allow electrical power generation for Kandahar City while the Northeast Power System (NEPS) – Southeast Power Systems (SEPS) connector is being completed. Norvane accomplishes all required commodity sourcing and delivery to points specified in the contract on a free on board (F.O.B.) Destination basis. Norvane is responsible for a performance-based contracting relationship, where its customer the US-Government specifies the desired end-state and Norvane executes an effective 'turn-key' sourcing solution for required commodities and all transportation to the specified delivery locations.
    </div>
  </section>

  <section class="panel panel--photo">
    <div class="refinery-photo" role="img" aria-label="Photo of an oil refinery lit at dusk, reflected in water"></div>
  </section>

  <section class="panel panel--blue">
    <h2 class="panel-title" style="left:17px;">OUR PROJECTS</h2>

    <h3 class="project-heading" style="left:17px; top:72px; width:350px;">Afghan Transportation Network (ATN) – South – Contract Number HTX483-14-D-R052</h3>
    <div class="project-body" style="left:17px; top:128px; width:351px;">
      <div class="project-photo" role="img" aria-label="Photo of a convoy of cargo trucks on a road" style="width:109px; height:75px; background:linear-gradient(160deg,#8a8f8c,#4c5248 55%,#2f3a2a);"></div>
      The Afghanistan Transportation Network (ATN) uses a network of U.S. Government (USG) approved Afghan privately owned trucking companies, otherwise known as Elder Owned Companies (EOCs) or locally-owned and locally-operated subcontractors. Norvane manages the approved EOCs or approved subcontractors to provide secure, reliable cargo and fuel transportation services to and from locations in the provinces of Day Kundi, Uruzgan, Zabul, and Kandahar of Afghanistan without the use of convoy security. The use of ATN regional transportation companies capitalizes on existing business agreements to promote the development of new business agreements with influential regional leaders. This capitalization of existing business agreements into new areas and companies allows Afghan infrastructure to develop, implement and sustain an Afghan-owned and operated transportation network capable of providing secure and reliable transportation of cargo.
    </div>

    <h3 class="project-heading" style="left:17px; top:253px; width:355px;">National Afghan Trucking II – Contract Number HTX483-14-D-R038</h3>
    <div class="project-body" style="left:17px; top:292px; width:351px;">
      <div class="project-photo" role="img" aria-label="Aerial photo of a desert road through dunes" style="width:109px; height:76px; background:linear-gradient(150deg,#c9a57a,#a07a52 50%,#d8bf98);"></div>
      The principal contract supporting the U.S. supply chain in Afghanistan is called National Afghan Trucking (NAT). Although there are other supply chain contracts, the NAT contracts provides trucking for over 70 percent of the total goods and materiel distributed to U.S. troops in the field. The trucks carry fuel, food, supplies, and heavy equipment. Norvane provides all management and logistics support resources necessary to pick-up cargo (material or equipment) at origin and delivers cargo to destination on Required Delivery Date (RDD) established by its customer. This includes proactive and competent management; well maintained logistics support resources, and trustworthy employees and subcontractors as necessary to facilitate dependable movement of cargo from origin to destination.
      <p style="margin-top:6px;">Norvane is constantly rated as one of the top carriers under this contract that is governed by the strict confines of a by the customer fully developed QA program detailed in an associated Quality Assurance Surveillance Plan (QASP) document that defines how performance standards will be applied; frequency of surveillance; and minimum acceptable defect rate(s).</p>
    </div>
  </section>

</main>
</body>
</html>
```